I need a business card for my original fine art pieces

I would like a business card design including a logo design for a new business in the art world. I am based in the Hunter Valley NSW Australia. I am a contemporary figurative, encaustic and wildlife artist. I would like to be able to upload my email and mobile number to this as well. This design should be one that I can incorporate into banners and flyers etc. Id like to incorporate one of my own images or partial image into the background or somewhere below. My initials are RJ and I would like these used as a logo type. I would like the use of some colour and it to be bright and catchy. The final design should communicate artwork custom made and commissions available.

Overview: Original Fine Artworks for sale, online, art galleries etc, Custom made to order and by commission.

Target market is world wide audience and corporate world

My figurative work is painted using acrylics in a lot of natural ochre colours that reflect the Australian Outback, on canvas, linen, paper or board: My encaustic work is created in a contemporary abstract style using a blow torch and a made with a medium of 100% pure bees wax, Damar resin, mixed media and coloured pigments, applied to Birch board. My wildlife are created using coloured pencil and mixed media on a variety of paper types or board.

```html
<!DOCTYPE html>
<html lang="en">
<head>
<meta charset="utf-8">
<title>Rhea Jansen – Business Card</title>
<link rel="stylesheet" href="https://fonts.googleapis.com/css2?family=Cinzel:wght@500&family=Source+Sans+3:wght@400;600&display=swap">
<style>
  :root {
    --stage: #000000;
    --card: #ff4a00;
    --ink: #ffffff;
    --serif: "Cinzel", "Times New Roman", serif;
    --sans: "Source Sans 3", "Myriad Pro", Arial, sans-serif;
  }
  * { margin: 0; padding: 0; box-sizing: border-box; }
  html, body { width: 1200px; height: 900px; overflow: hidden; background: var(--stage); }
  .stage { position: relative; width: 1200px; height: 900px; }

  .card {
    position: absolute; top: 275px; width: 477px; height: 293px;
    background: var(--card); color: var(--ink); overflow: hidden;
  }
  .card--front { left: 116px; border-radius: 0 52px 0 52px; }
  .card--back  { left: 622px; border-radius: 52px 0 52px 0; }

  /* front */
  .holder { position: absolute; right: 19px; top: 34px; text-align: right; font-family: var(--sans); }
  .holder__name { font-size: 20px; font-weight: 600; line-height: 24px; }
  .holder__role { font-size: 13.5px; font-weight: 400; line-height: 18px; }

  .brand-dot {
    position: absolute; left: 110px; top: 73px; width: 94px; height: 94px;
    border: 2.5px solid var(--ink); border-radius: 50%;
  }
  .brand { position: absolute; text-align: center; }
  .brand__name { font-family: var(--serif); font-weight: 500; white-space: nowrap; }
  .brand__tag { font-family: var(--sans); font-weight: 400; white-space: nowrap; }

  .card--front .brand { left: 14px; width: 286px; top: 166px; }
  .card--front .brand__name { font-size: 33px; line-height: 38px; letter-spacing: 0.3px; }
  .card--front .brand__tag { font-size: 13.5px; letter-spacing: 3.1px; line-height: 16px; }

  .contacts { position: absolute; right: 19px; top: 216px; list-style: none; font-family: var(--sans); font-size: 13.5px; }
  .contacts li { display: flex; justify-content: flex-end; align-items: center; gap: 8px; height: 17.5px; }
  .contacts svg { width: 10px; height: 10px; fill: var(--ink); }

  /* back */
  .card--back .brand { left: 0; width: 477px; top: 213px; }
  .card--back .brand__name { font-size: 36px; line-height: 40px; letter-spacing: 0.3px; }
  .card--back .brand__tag { font-size: 15px; letter-spacing: 3.2px; line-height: 18px; }
</style>
</head>
<body>
<main class="stage">
  <section class="card card--front">
    <div class="holder">
      <p class="holder__name">Daniel Carter</p>
      <p class="holder__role">Managing Director</p>
    </div>
    <div class="brand-dot" aria-hidden="true"></div>
    <div class="brand">
      <p class="brand__name">Rhea Jansen</p>
      <p class="brand__tag">ORIGINAL FINE ARTWORKS</p>
    </div>
    <ul class="contacts">
      <li>044-987 650 321
        <svg viewBox="0 0 10 10"><path d="M2 0.5 L3.6 2.6 L2.8 3.6 Q3.8 5.7 6.2 7 L7.3 6.2 L9.5 7.9 L8.3 9.5 Q4.3 9.2 0.5 1.8 Z"/></svg></li>
      <li>hello@rjstudio.com
        <svg viewBox="0 0 10 10"><path d="M0 2 H10 V8.5 H0 Z M0.8 2.6 L5 5.6 L9.2 2.6" stroke="#ff4a00" stroke-width="0.8"/></svg></li>
      <li>www.rheajansenart.com
        <svg viewBox="0 0 10 10"><path d="M4 6 L6 4 M3.2 5 L1.6 6.6 A1.5 1.5 0 0 0 3.4 8.4 L5 6.8 M6.8 5 L8.4 3.4 A1.5 1.5 0 0 0 6.6 1.6 L5 3.2" stroke="#fff" stroke-width="1.1" fill="none"/></svg></li>
    </ul>
  </section>

  <section class="card card--back">
    <div class="brand">
      <p class="brand__name">Rhea Jansen</p>
      <p class="brand__tag">ORIGINAL FINE ARTWORKS</p>
    </div>
  </section>
</main>
</body>
</html>
```